LIFE CHANGING NEW WEBSITE DESIGN NEEDED FOR FULL WEBSITE- FUN/FEMININE!

I need a website designed for a personal financial advice website geared at women called BLUE OTTER LANTERN. I will be providing free financial advice around topics of making, saving, spending and sharing money. The concept is to change the way women understand money and the necessity around building various passive income streams to ensure full financial freedom. This will then carry down to advice for mothers with children and children in particular. The website should be elegant and yet witty. I don't want lots of serious photos but more relatable. I will have a photo of myself and my story as this is a blog and needs to be relatable to women and mothers. I like pinks and greys. I want to have a pink piggy bank being broken with a hammer in the front screen to break our traditional mindset around piggy bank saving/spending habits. I have created a logo that is a pink piggy head with BLUE OTTER LANTERN that needs to be incorporated so that it blends into the heading. I have also already started designing the website on Squarespace and can provide access to that. Basically it should have a format of BLUE OTTER LANTERN LOGO center in header then on left hand navigation: MAKE, SAVE, SPEND, SHARE then on right hand header navigation: MISSION, GET STARTED, CONTACT BOL I would like to have the front page when you go to the url to have the image of the piggy bank being broken then a catchy phrase then under 4 boxes with MAKE (image and description) SAVE (image and description) SPEND (image and description) SHARE (image and description) if you click on those or the title they go to pages that are dedicated to each them. Each page should have a little intro on the topic then I want lots of blog links as I will be mainly writing blogs. Each blog site should have ability to write comments as well. I need social media icons on each page too. Please let me know what you need from me to get started. I prefer having a discussion if possible to not waste anyone's time. I need the site to be easy for me to use and add blogs/urls etc as needed. I also need the site to be put into my domain that I already purchased: www.blueotterlantern-sample.com

Target Market(s)

teenage girls, 20 something girls, 30 something girls and mothers

Coding

Coded - Design and coding required

Number of Pages Required

5+ page

Font styles to use
Sans Serif

Colors
e667a6
e34197
f59195
eea4c8
aaaaaa
cbcbcb
959595

Requirements
Must have
• TOP NAVIGATION
• MAKE SAVE SPEND SHARE LOGO/BLUE OTTER LANTERN MISSION GET STARTED CONTACT BOL
• FRONT PAGE: IMAGE OF PIGGY BANK BEING BROKEN WITH A HAMMER
• CATCH PHRASE OVER THE IMAGE
• BUTTON IN PINK- TAKE ACTION (WHICH DIRECTS TO TAKE ACTION TAB ON NAVIGATION HEADER
• 4 BOXES BELOW MAIN IMAGE WITH IMAGE/DESCRIPTIONS FOR MAKE, SAVE, SPEND, SHARE THAT EACH GO TO THE PAGES FROM THE NAVIGATION HEADER
• EACH PAGE SHOULD BE DEDICATED TO THOSE TOPICS THEN THERE IS AN INTRO ON EACH PAGE THEN THE LINKS TO DIFFERENT BLOGS AROUND EACH TOPIC FOR MAKE, SAVE, SPEND, SHARE
• EACH BLOG SHOULD HAVE COMMENTS SECTION AND SOCIAL MEDIA ICONS
• (GOOD TO USE PINKS/GREYS)
Should not have
• BE SUPER BUSY, CLUTTERED, FEEL LIKE I AM SELLING SOMETHING

```html
<!DOCTYPE html>
<html lang="en">
<head>
<meta charset="utf-8">
<title>Blue Otter Lantern</title>
<link href="https://fonts.googleapis.com/css2?family=Lato:wght@400;700;900&display=swap" rel="stylesheet">
<style>
:root{
  --pink-deep:#d6076f;
  --pink-band:#f07a83;
  --pink-tag:#ec93bf;
  --pink-logo:#e3419b;
  --ink:#333333;
  --grey-card:#f1f1f1;
  --grey-text:#4a4a4a;
  --footer:#2a2a2a;
  --white:#ffffff;
}
*{box-sizing:border-box;margin:0;padding:0}
html,body{width:1200px;height:2809px;overflow:hidden}
body{font-family:'Lato',sans-serif;color:var(--ink);background:var(--white);position:relative}
.abs{position:absolute}

/* header */
.site-header{position:absolute;top:0;left:0;width:1200px;height:133px;background:var(--white)}
.nav{position:absolute;top:60px;display:flex;gap:42px;font-size:14px;font-weight:700;letter-spacing:.2px;color:#333}
.nav-left{left:74px}
.nav-right{right:74px}
.brand{position:absolute;left:0;width:1200px;top:32px;text-align:center}
.brand-mark{display:block;margin:0 auto 4px;width:40px;height:40px;border:3px solid var(--pink-logo);border-radius:50%}
.brand-name{font-size:22px;color:var(--pink-logo);font-weight:400}

/* hero */
.hero{position:absolute;top:133px;left:0;width:1200px;height:590px}
.hero-copy{position:absolute;left:74px;top:170px;color:var(--white)}
.hero-title{font-size:57px;font-weight:900;letter-spacing:-.5px;line-height:1}
.hero-sub{margin-top:20px;font-size:22px;line-height:32px;width:560px;font-weight:700}
.btn{display:inline-block;background:var(--pink-deep);color:var(--white);font-weight:700;font-size:17px;text-align:center;border-radius:24px;width:208px;height:46px;line-height:46px}
.hero .btn{margin-top:24px;margin-left:2px}

/* topic cards */
.topics{position:absolute;top:792px;left:75px;display:flex;gap:29px}
.topic-card{width:241px;height:485px;background:var(--grey-card);border-radius:120px 120px 40px 40px;text-align:center;padding-top:16px}
.topic-photo{width:210px;height:210px;margin:0 auto;border-radius:50%;border-bottom:4px solid var(--pink-deep)}
.topic-title{margin-top:26px;font-size:22px;font-weight:900;color:var(--pink-deep)}
.topic-text{margin:10px 16px 0;font-size:15px;line-height:26px;color:var(--grey-text)}

/* welcome band */
.welcome{position:absolute;top:1325px;left:0;width:1200px;height:590px}
.welcome-copy{position:absolute;top:120px;left:72px;width:1056px;text-align:center;color:var(--white)}
.welcome-title{font-size:28px;font-weight:900;margin-bottom:22px}
.welcome-copy p{font-size:16.4px;line-height:28px;margin-bottom:17px}
.welcome .btn{margin-top:18px}

/* blog */
.blog-heading{position:absolute;top:1963px;width:1200px;text-align:center;font-size:28px;font-weight:900;color:#333}
.posts{position:absolute;top:2032px;left:75px;display:flex;gap:29px}
.post{width:331px}
.post-photo{height:188px}
.post-tag{display:inline-block;margin-top:22px;background:var(--pink-tag);color:var(--white);font-size:13px;font-weight:700;padding:0 14px;height:28px;line-height:28px}
.post-title{margin-top:12px;font-size:20px;font-weight:700;line-height:25px;color:#333}
.post-date{margin-top:6px;font-size:13px;font-weight:700;color:var(--pink-deep);display:flex;align-items:center;gap:20px}
.post-date i{display:inline-block;width:12px;height:12px;background:var(--pink-deep);border-radius:2px}
.post-text{margin-top:10px;font-size:14.2px;line-height:24px;color:var(--grey-text)}
.comment{margin-top:12px;height:39px;border:1px solid #cbcbcb;font-size:12px;color:#666;padding:0 12px;line-height:37px}
.social{display:flex;gap:14px;margin-top:20px}
.social span{width:13px;height:13px;border-radius:50%;background:#666}

/* footer */
.site-footer{position:absolute;top:2590px;left:0;width:1200px;height:219px;background:var(--footer);color:var(--white)}
.foot-brand{position:absolute;left:75px;top:42px}
.foot-brand .brand-mark{margin:0 0 4px 68px;width:34px;height:34px}
.foot-brand .brand-name{font-size:19px}
.copyright{position:absolute;left:75px;top:128px;font-size:12.5px;line-height:21px}
.foot-head{position:absolute;top:40px;font-size:15px;font-weight:700}
.foot-links{position:absolute;font-size:14.5px;line-height:29px}
.email{position:absolute;left:624px;top:84px;width:243px;height:38px;border:1px solid #ccc;font-size:13px;line-height:36px;padding-left:14px}
.signup{position:absolute;left:624px;top:138px;width:77px;height:38px;background:var(--pink-band);font-size:13px;font-weight:700;line-height:38px;text-align:center}
.foot-social{position:absolute;left:925px;top:84px;display:flex;gap:18px}
.foot-social span{width:18px;height:18px;border-radius:50%;background:#e5e5e5}
</style>
</head>
<body>

<header class="site-header">
  <nav class="nav nav-left"><span>MAKE</span><span>SAVE</span><span>SPEND</span><span>SHARE</span></nav>
  <div class="brand"><span class="brand-mark"></span><span class="brand-name">Blue Otter Lantern</span></div>
  <nav class="nav nav-right"><span>MISSION</span><span>GET STARTED</span><span>CONTACT BOL</span></nav>
</header>

<section class="hero">
  <svg class="abs" width="1200" height="590" viewBox="0 0 1200 590" role="img" aria-label="Pink piggy bank being broken by a hammer on a wooden table with scattered coins and notes">
    <defs>
      <linearGradient id="heroGrad" x1="0" y1="0" x2="1" y2="0.3">
        <stop offset="0" stop-color="#4a3424"/>
        <stop offset=".45" stop-color="#6a4c34"/>
        <stop offset=".7" stop-color="#a85f57"/>
        <stop offset="1" stop-color="#7a6a55"/>
      </linearGradient>
    </defs>
    <path d="M0 0H1200V555C1100 575 1000 590 850 585C650 578 450 565 300 582C180 596 80 565 0 560Z" fill="url(#heroGrad)"/>
  </svg>
  <div class="hero-copy">
    <h1 class="hero-title">BLUE OTTER LANTERN.</h1>
    <p class="hero-sub">Get a free financial advice around topics of making, saving, spending and sharing money..</p>
    <span class="btn">TAKE ACTION</span>
  </div>
</section>

<section class="topics">
  <article class="topic-card">
    <div class="topic-photo" role="img" aria-label="Woman at a laptop with banknotes" style="background:linear-gradient(135deg,#c9d3dc,#6d89b2)"></div>
    <h2 class="topic-title">MAKE</h2>
    <p class="topic-text">Lorem ipsum dolor sit amet, consectetur adipiscing elit. Duis ultrices odio sit amet ex ultricies euismoded id varius lectus. Etiam id tortor semper, viverra metus et</p>
  </article>
  <article class="topic-card">
    <div class="topic-photo" role="img" aria-label="Mother and daughter with a piggy bank" style="background:linear-gradient(135deg,#d8c7a6,#8a6a5a)"></div>
    <h2 class="topic-title">SAVE</h2>
    <p class="topic-text">Lorem ipsum dolor sit amet, consectetur adipiscing elit. Duis ultrices odio sit amet ex ultricies euismoded id varius lectus. Etiam id tortor semper, viverra metus et</p>
  </article>
  <article class="topic-card">
    <div class="topic-photo" role="img" aria-label="Woman holding a fan of banknotes before a chalkboard" style="background:linear-gradient(135deg,#7f8a86,#c9a43a)"></div>
    <h2 class="topic-title">SPEND</h2>
    <p class="topic-text">Lorem ipsum dolor sit amet, consectetur adipiscing elit. Duis ultrices odio sit amet ex ultricies euismoded id varius lectus. Etiam id tortor semper, viverra metus et</p>
  </article>
  <article class="topic-card">
    <div class="topic-photo" role="img" aria-label="Advisor explaining papers to a client" style="background:linear-gradient(135deg,#b9b3ad,#2e2a2a)"></div>
    <h2 class="topic-title">SHARE</h2>
    <p class="topic-text">Lorem ipsum dolor sit amet, consectetur adipiscing elit. Duis ultrices odio sit amet ex ultricies euismoded id varius lectus. Etiam id tortor semper, viverra metus et</p>
  </article>
</section>

<section class="welcome">
  <svg class="abs" width="1200" height="590" viewBox="0 0 1200 590">
    <path d="M0 20C150 45 300 45 450 30C650 5 800 40 950 42C1080 44 1150 30 1200 12V540C1050 560 900 560 700 553C500 546 350 590 200 580C120 575 50 565 0 560Z" fill="var(--pink-band)"/>
    <path d="M700 40C850 45 1000 48 1200 8V1C1050 30 900 45 700 40Z" fill="var(--pink-deep)"/>
    <path d="M0 560C60 568 130 580 220 582C350 590 480 560 600 552C450 555 330 585 200 574C120 570 60 560 0 552Z" fill="var(--pink-deep)"/>
  </svg>
  <div class="welcome-copy">
    <h2 class="welcome-title">WELCOME TO BLUE OTTER LANTERN (BOL)!</h2>
    <p>My mission is simple- I want to challenge you to rethink the way you think about growing, spending and saving money. By redesigning your life around your finances I want you to run your life as if you are the CEO of your own business, and the business is maximising the value and profitability of your life.</p>
    <p>It is shocking that in today’s world of information we are we still live in a society where most educated people leave school without even a basic understanding of money and how to run their lives outside of a just obtaining a job. Instead, we are taught to work hard in school, find a good job, get married, have children, save up for big expenses (like homes, school tuition..) then retire. By completely lacking personal finance education in schools and few resources to help,&nbsp; it is little wonder that life often feels like one big rat race of no end.</p>
    <span class="btn">READ MORE</span>
  </div>
</section>

<h2 class="blog-heading">BLOG POSTS</h2>
<section class="posts">
  <article class="post">
    <div class="post-photo" role="img" aria-label="Two businesswomen in discussion at a table" style="background:linear-gradient(135deg,#e6e9ec,#8c7f80)"></div>
    <span class="post-tag">MAKE</span>
    <h3 class="post-title">ALIQUAM CONSEQUAT IN DUI VEL CONDIMENTUM</h3>
    <div class="post-date"><i></i>JUN 20, 2019</div>
    <p class="post-text">Nunc ante sapien, scelerisque eget velit eu, placerat molestie ligula. Vestibulum ante ipsum primis in faucibus orci luctus et ultrices posuere..</p>
    <div class="comment">Enter comment..</div>
    <div class="social" aria-label="Social links"><span></span><span></span><span></span><span></span><span></span></div>
  </article>
  <article class="post">
    <div class="post-photo" role="img" aria-label="Person in white shirt holding banknotes on yellow" style="background:linear-gradient(90deg,#f0e21a,#f3f0e8 45%,#b9a410)"></div>
    <span class="post-tag">SPEND</span>
    <h3 class="post-title">ALIQUAM CONSEQUAT IN DUI VEL CONDIMENTUM</h3>
    <div class="post-date"><i></i>JUN 20, 2019</div>
    <p class="post-text">Nunc ante sapien, scelerisque eget velit eu, placerat molestie ligula. Vestibulum ante ipsum primis in faucibus orci luctus et ultrices posuere..</p>
    <div class="comment">Enter comment..</div>
    <div class="social" aria-label="Social links"><span></span><span></span><span></span><span></span><span></span></div>
  </article>
  <article class="post">
    <div class="post-photo" role="img" aria-label="Smiling woman in yellow with a piggy bank" style="background:linear-gradient(135deg,#f4e9d2,#e8b33a 55%,#d9dfd2)"></div>
    <span class="post-tag">SAVE</span>
    <h3 class="post-title">ALIQUAM CONSEQUAT IN DUI VEL CONDIMENTUM</h3>
    <div class="post-date"><i></i>JUN 20, 2019</div>
    <p class="post-text">Nunc ante sapien, scelerisque eget velit eu, placerat molestie ligula. Vestibulum ante ipsum primis in faucibus orci luctus et ultrices posuere..</p>
    <div class="comment">Enter comment..</div>
    <div class="social" aria-label="Social links"><span></span><span></span><span></span><span></span><span></span></div>
  </article>
</section>

<footer class="site-footer">
  <div class="foot-brand"><span class="brand-mark"></span><span class="brand-name">Blue Otter Lantern</span></div>
  <p class="copyright">Copyright © 2019. Company Name.<br>All Right Reserved</p>
  <h4 class="foot-head" style="left:346px">SITE MAP</h4>
  <div class="foot-links" style="left:346px;top:70px">Make<br>Save<br>Spend<br>Share</div>
  <div class="foot-links" style="left:462px;top:74px;line-height:31px">Mission<br>Get Started<br>Contact Bol</div>
  <h4 class="foot-head" style="left:624px">EMAIL SIGN UP</h4>
  <div class="email">Enter Email Address</div>
  <div class="signup">SIGN UP</div>
  <h4 class="foot-head" style="left:925px">FOLLOW US</h4>
  <div class="foot-social" aria-label="Social links"><span></span><span></span><span></span><span></span><span></span></div>
</footer>

</body>
</html>
```